Namecard for wristwatch company

I run a watch company named Varnik which just launched our first watch. I need a namecard design that is unique and something very different. It should be the same size or smaller than the usual cards. It will be printed on the usual paper as metal/wood are nice but might be too expensive.
I have attached some photos of my watch and the company logo as well.

Target Market(s)
Watch collectors, young professionals
Industry/Entity Type
It Company
Look and feel

```html
<!DOCTYPE html>
<html lang="en">
<head>
<meta charset="UTF-8">
<title>Varnik Business Card</title>
<link href="https://fonts.googleapis.com/css2?family=Aldrich&display=swap" rel="stylesheet">
<style>
  :root{
    --page:#e6e7e9;
    --card-light:#ffffff;
    --card-grey:#d4d6d8;
    --brand-blue:#00aeef;
    --ink:#3d3f42;
    --ink-soft:#55585c;
    --white:#ffffff;
  }
  *{margin:0;padding:0;box-sizing:border-box}
  html,body{width:1200px;height:870px;overflow:hidden}
  body{background:var(--page);font-family:"Aldrich",sans-serif;position:relative}

  .card{
    position:absolute;width:580px;height:332px;
    box-shadow:0 10px 28px rgba(0,0,0,.22);overflow:hidden;
    background:linear-gradient(160deg,var(--card-light) 0%,var(--card-grey) 100%);
  }
  .card--back{left:70px;top:70px}
  .card--front{left:550px;top:468px}

  .logo{
    position:absolute;width:128px;height:128px;border:5px solid var(--ink);
    border-radius:50%;display:flex;align-items:center;justify-content:center;
    color:var(--brand-blue);font-size:27px;letter-spacing:1px;
  }
  .card--back .logo{left:226px;top:102px}
  .card--front .logo{right:60px;top:72px;background:transparent}

  .contact-list{position:absolute;left:40px;top:26px;list-style:none}
  .contact-list li{display:flex;align-items:center;gap:10px;height:25px;font-size:14px;color:var(--ink-soft)}
  .contact-list svg{width:14px;height:14px;fill:var(--ink)}

  .band{
    position:absolute;left:0;right:0;bottom:0;height:146px;background:var(--brand-blue);color:var(--white);
  }
  .address{position:absolute;left:40px;top:22px;font-size:17px;line-height:24px}
  .person{position:absolute;right:34px;bottom:24px;text-align:right}
  .person__name{font-size:19px;letter-spacing:1px}
  .person__role{font-size:15px;margin-top:3px}
</style>
</head>
<body>
  <section class="card card--back" aria-label="Card back">
    <div class="logo">Varnik</div>
  </section>

  <section class="card card--front" aria-label="Card front">
    <ul class="contact-list">
      <li><svg viewBox="0 0 24 24"><path d="M6.6 10.8a15 15 0 0 0 6.6 6.6l2.2-2.2c.3-.3.7-.4 1-.2 1.1.4 2.3.6 3.6.6.6 0 1 .4 1 1V20c0 .6-.4 1-1 1A17 17 0 0 1 3 4c0-.6.4-1 1-1h3.5c.6 0 1 .4 1 1 0 1.3.2 2.5.6 3.6.1.3 0 .7-.2 1z"/></svg>014 282 5930</li>
      <li><svg viewBox="0 0 24 24"><path d="M7 1h10a2 2 0 0 1 2 2v18a2 2 0 0 1-2 2H7a2 2 0 0 1-2-2V3a2 2 0 0 1 2-2zm0 3v14h10V4z"/></svg>014 282 5931</li>
      <li><svg viewBox="0 0 24 24"><path d="M6 2h9v6H6zM3 9h18v13H3zm4 3v2h3v-2zm5 0v2h3v-2zm-5 4v2h3v-2zm5 0v2h3v-2z"/></svg>014 282 5932</li>
      <li><svg viewBox="0 0 24 24"><path d="M2 5h20v14H2zm2 2v.5l8 5 8-5V7l-8 5z"/></svg>milo@varnik.co</li>
      <li><svg viewBox="0 0 24 24"><path d="M12 2a10 10 0 1 0 0 20 10 10 0 0 0 0-20zm6.9 6h-3a15 15 0 0 0-1.3-3.9A8 8 0 0 1 18.9 8zM12 4c.8 1.2 1.5 2.5 1.9 4h-3.8c.4-1.5 1.1-2.8 1.9-4zM4.3 14a8 8 0 0 1 0-4h3.4a16 16 0 0 0 0 4zm.8 2h3a15 15 0 0 0 1.3 3.9A8 8 0 0 1 5.1 16zm3-8h-3a8 8 0 0 1 4.3-3.9C8.9 5.3 8.4 6.6 8.1 8zM12 20c-.8-1.2-1.5-2.5-1.9-4h3.8c-.4 1.5-1.1 2.8-1.9 4zm2.3-6H9.7a14 14 0 0 1 0-4h4.6a14 14 0 0 1 0 4zm.3 5.9c.6-1.2 1-2.5 1.3-3.9h3a8 8 0 0 1-4.3 3.9zm1.7-5.9a16 16 0 0 0 0-4h3.4a8 8 0 0 1 0 4z"/></svg>www.varnik.co</li>
    </ul>

    <div class="logo">Varnik</div>

    <div class="band">
      <p class="address">214.9th floor.Quay<br>Harbor Lane RDX</p>
      <div class="person">
        <p class="person__name">MILO BRENNAN</p>
        <p class="person__role">Managing Director</p>
      </div>
    </div>
  </section>
</body>
</html>
```